Tree Pruning Website

We need a website for a tree Arborist, pruning company called Maple Crest Canopy Works. We look after all types of trees, knock down trees and prune trees. Our target market is from domestic clients to government clients and everything in between.

We would like to see the use of our main colours which are orange and green

We are not looking forward in seeing a template that we have seen before but a unique template. We have designed 5 templates ourselves and we wish for the design community to take our designs to the next level.

We have also designed a template for things that **we are not** looking for (Version 4)

To make it fair for everyone, we are also not giving out any participation payments as we have had. One winner will take all of the payment!!!

I Have attached a image of the designs and a image of a tree.

We are just looking at the PSD file been developed. We have our own team who can slice the image up into a HTML format.

Target Market(s)

Everyone who needs to cut down a tree

Industry/Entity Type

Government

Requirements
Must have
• Logo on front page
A List of our services
jQuery slider on page
Phone Number on every page

```html
<!DOCTYPE html>
<html lang="en">
<head>
<meta charset="utf-8">
<title>Maple Crest Canopy Works</title>
<link rel="stylesheet" href="https://fonts.googleapis.com/css2?family=Oswald:wght@300;400&family=PT+Sans:wght@400;700&display=swap">
<style>
:root{
  --green:#56a830;
  --green-dark:#3f8a20;
  --green-text:#5aa83a;
  --page:#f4f2f2;
  --header:#f8f6f0;
  --gold:#d89a2a;
  --white:#ffffff;
  --red:#e0262a;
}
*{margin:0;padding:0;box-sizing:border-box}
html,body{width:1200px;height:1193px;overflow:hidden}
body{position:relative;background:var(--page);font-family:Arial,Helvetica,sans-serif;color:var(--green-text)}
.abs{position:absolute}
.header{left:0;top:0;width:1200px;height:123px;background:var(--header)}
.brand{left:187px;top:40px;display:flex;align-items:center;gap:10px}
.brand-mark{width:26px;height:26px;border-radius:50%;background:var(--green)}
.brand-name{font-family:"Oswald",sans-serif;font-weight:400;font-size:26px;color:var(--green);line-height:1.1;width:190px}
.call{left:914px;top:22px;font-family:"Oswald",sans-serif;font-weight:300;font-size:14px;color:var(--green)}
.nav{left:512px;top:40px;height:83px;display:flex;list-style:none}
.nav li{font-family:"Oswald",sans-serif;font-weight:400;font-size:14px;letter-spacing:.6px;color:var(--green-dark);padding:0 14px;line-height:104px;height:83px}
.nav li.active{background:linear-gradient(#f8f6f0,#8fcf6d 55%,#6cbb4a);color:var(--white);padding:0 16px;width:65px}
.hero{left:0;top:123px;width:1200px;height:429px;background:radial-gradient(ellipse at 50% 30%,#f0e2b6 0%,#e5b24a 45%,#c98a1c 85%)}
.slide-frame{left:187px;top:168px;width:826px;height:335px;background:#e8d6a0;box-shadow:0 6px 18px rgba(0,0,0,.25)}
.slide{left:195px;top:176px;width:810px;height:319px;background:linear-gradient(160deg,#4a6aa8 0%,#5f6f3e 35%,#d8d0c2 55%,#4e5a36 80%,#c4b8a4 100%)}
.dots{left:548px;top:522px;display:flex;gap:11px}
.dots span{width:12px;height:12px;border-radius:50%;background:#e8c98a}
.dots span.on{background:var(--white)}
h2{font-family:"Oswald",sans-serif;font-weight:400;font-size:29px;color:var(--green);letter-spacing:-.5px}
.welcome{left:176px;top:562px;width:512px}
.welcome p{font-size:10px;line-height:14px;margin-top:14px;text-align:justify}
.btn{display:inline-block;margin-top:26px;background:var(--green);color:var(--white);font-weight:bold;font-size:12px;padding:9px 18px;border-radius:2px}
.video-title{left:725px;top:562px}
.video{left:724px;top:616px;width:296px;height:172px;background:var(--green);border-radius:4px;padding:5px}
.video-screen{position:relative;width:100%;height:100%;background:linear-gradient(120deg,#6b6a55,#a29a86 50%,#5a5a48)}
.video-bar{position:absolute;left:10px;right:14px;bottom:6px;height:22px;background:rgba(30,30,30,.75);display:flex;align-items:center;gap:8px;padding:0 6px}
.video-bar .track{flex:1;height:4px;background:#ddd;border-radius:2px}
.box{top:812px;height:196px}
.box .tab{position:absolute;left:0;top:0;height:38px;background:var(--green);font-family:"Oswald",sans-serif;font-size:23px;color:var(--white);padding:2px 0 0 22px}
.box .body{position:absolute;left:0;top:38px;right:0;bottom:0;background:var(--green);padding:16px 18px;color:var(--white);font-size:10.5px;line-height:12.5px;text-align:justify}
.box .body p{margin-bottom:10px}
.box .more{position:absolute;left:18px;bottom:18px;text-decoration:underline;font-size:11px}
.gallery-img{position:absolute;left:10px;top:10px;right:10px;bottom:10px;background:linear-gradient(#b8c0b0,#6e8a4a 55%,#3c5a22)}
.arrow{top:823px;width:17px;height:17px;border-radius:50%;background:var(--green)}
.footer{left:0;top:1034px;width:1200px;height:159px;background:var(--green);color:var(--white);font-family:"PT Sans",sans-serif}
.news{left:178px;top:21px;width:229px;height:101px;background:var(--white);border:4px solid;border-image:repeating-linear-gradient(45deg,#d33 0 6px,#fff 6px 10px,#36c 10px 16px,#fff 16px 20px) 4;padding:8px 12px;color:#666}
.news h3{font-size:15px;font-weight:700;color:#777}
.news .field{display:flex;margin-top:4px;border:1px solid #ccc;height:22px;font-size:11px;align-items:center}
.news .field span{flex:1;padding-left:8px;color:#999}
.news .field b{background:var(--red);color:var(--white);height:20px;line-height:20px;padding:0 8px;border-radius:3px;font-size:11px}
.news p{font-size:10.5px;line-height:13px;margin-top:6px}
.fcol h4{font-size:12px;font-weight:700;margin-bottom:20px}
.fcol li{list-style:none;font-size:11.5px;line-height:21px}
.contact li{line-height:17px}
.contact li em{font-style:normal;display:inline-block;width:29px}
.social{display:flex;gap:7px;margin-top:-2px}
.social span{width:27px;height:27px;border-radius:50%;background:var(--white);border:2px solid #d8e8cc}
.legal{font-size:11.5px;line-height:19px;margin-top:10px}
</style>
</head>
<body>
<header class="header abs">
  <div class="brand abs"><span class="brand-mark"></span><span class="brand-name">Maple Crest Canopy Works</span></div>
  <div class="call abs">Call Us: 0207-88-312</div>
  <ul class="nav abs">
    <li class="active">Home</li><li>About Us</li><li>Our Services</li><li>Our Work</li><li>Get a Quote</li><li>Contact Us</li>
  </ul>
</header>

<section class="hero abs" role="img" aria-label="Blurred golden field with a tree in the background"></section>
<div class="slide-frame abs"></div>
<div class="slide abs" role="img" aria-label="Looking up into pale-barked gum tree branches against a blue sky"></div>
<div class="dots abs"><span></span><span></span><span class="on"></span><span></span><span></span></div>

<section class="welcome abs">
  <h2>Welcome to Maple Crest Canopy Works</h2>
  <p>At vero eos et accusamus et iusto odio dignissimos ducimus qui blanditiis praesentium voluptatum deleniti atque corrupti quos dolores etquas molestias excepturi sint occaecati cupiditate non provident, similique sunt in culpa qui officia deserunt mollitia animi, ililaborum et dolorum fuga. Et harum quidem rerum facilis est et expedita distinctio.</p>
  <p>Nam libero tempore, cum soluta nobis est eligendi optio cumque nihil impedit quo minus id quod maxime placeat facere possili, omnis voluptas assumenda est, omnis dolor repellendus. At vero eos et accusamus et iusto odio dignissimos ducimus qui blanditiis praesentium voluptatum deleniti atque corrupti quos dolores etquas molestias excepturi sint occaecati cupiditate non provident,</p>
  <span class="btn">View More</span>
</section>

<h2 class="video-title abs">Our Video</h2>
<div class="video abs">
  <div class="video-screen" role="img" aria-label="Video still of a worker cutting a large tree stump">
    <svg class="abs" style="left:128px;top:54px" width="44" height="40" viewBox="0 0 44 40"><path d="M4 4 L40 20 L4 36 L12 20 Z" fill="#fff" opacity=".9"/></svg>
    <div class="video-bar"><svg width="12" height="12" viewBox="0 0 12 12"><path d="M2 1 L11 6 L2 11 Z" fill="#fff"/></svg><span class="track"></span><svg width="10" height="10" viewBox="0 0 10 10"><path d="M1 1h3M1 1v3M9 1h-3M9 1v3M1 9h3M1 9v-3M9 9h-3M9 9v-3" stroke="#fff"/></svg></div>
  </div>
</div>

<section class="box abs" style="left:176px;width:274px">
  <div class="tab" style="width:152px">Our Services</div>
  <div class="body">
    <p>Our commitment to providing value-packed, quality-approved food service is matched only by our steadfast dedication to sustainable industry practices.</p>
    <p>We're the local leader in meatless mobility spreading the bread with love and spreading the word about the virtues of alternative eating options.</p>
    <span class="more">View More...</span>
  </div>
</section>
<section class="box abs" style="left:462px;width:274px">
  <div class="tab" style="width:152px">Our Blog</div>
  <div class="body" style="text-align:left">
    <p>Another first for San Francisco. Bright Harvest is ahead of the international trend with a clever combination of culinary and technological innovation.</p>
    <p>Our 5 rooftop solar panels create additional energy to run a blender, toaster and other appliances, and reduce the need for a generator.</p>
    <span class="more">View More...</span>
  </div>
</section>
<section class="box abs" style="left:748px;width:275px">
  <div class="tab" style="width:152px">Photo Gallery</div>
  <div class="body"><div class="gallery-img" role="img" aria-label="Large green tree on a grassy hill under a cloudy sky"></div></div>
</section>
<svg class="arrow abs" style="left:976px" viewBox="0 0 17 17"><circle cx="8.5" cy="8.5" r="8.5" fill="#56a830"/><path d="M10 5 L6.5 8.5 L10 12" stroke="#fff" stroke-width="2" fill="none"/></svg>
<svg class="arrow abs" style="left:1003px" viewBox="0 0 17 17"><circle cx="8.5" cy="8.5" r="8.5" fill="#56a830"/><path d="M7 5 L10.5 8.5 L7 12" stroke="#fff" stroke-width="2" fill="none"/></svg>

<footer class="footer abs">
  <div class="news abs">
    <h3>Join Our Newsletter</h3>
    <div class="field"><span>Enter Your Email Address</span><b>Sign Up</b></div>
    <p>Signup to receive invite to special events, parties, cooking demos, coupons</p>
  </div>
  <div class="fcol abs" style="left:456px;top:22px">
    <h4>Company</h4>
    <ul><li>Privacy</li><li>Terms Of Use</li><li>Terms Of Trade</li><li>PO T&amp;C's</li></ul>
  </div>
  <div class="fcol contact abs" style="left:596px;top:22px">
    <h4>Contact Us</h4>
    <ul><li>Level 9 214 Ashgrove Lane</li><li>Fernvale Vic 3921</li><li><em>T:</em>+61 3 5550 4821</li><li><em>F:</em>+61 3 5550 4829</li><li><em>E:</em>info@maplecrestcanopy.com</li></ul>
  </div>
  <div class="fcol abs" style="left:802px;top:22px">
    <h4>Follow Us Online</h4>
    <div class="social"><span></span><span></span><span></span><span></span></div>
    <p class="legal">Privacy Policy | Terms of Services | Sitemap<br>Copyright © 2013. All Rights Reserved.</p>
  </div>
</footer>
</body>
</html>
```